Water ATM Card

Need a design for water ATM cards. Size of card is 3.375 x 2.125 inch
On the Front include the Cedar hollow Logo.
Bottom right corner should have Price $100
On the Back
This card is to be used to access water refills at any Cedar Hollow Water Vending Machines.
Please contact (869) 418 2930 or (869) 534 1276 or email clearflowbox@mailvista.example for any assistance or recharging of card.

```html
<!DOCTYPE html>
<html lang="en">
<head>
<meta charset="UTF-8">
<title>Cedar Hollow Water ATM Card</title>
<link rel="stylesheet" href="https://fonts.googleapis.com/css2?family=Montserrat:wght@600;700;800&display=swap">
<style>
  :root {
    --bg: #e6e8eb;
    --card: #ffffff;
    --ink: #111111;
    --brand-blue: #1f6fc0;
    --band-blue: #1e7fd0;
    --band-green: #3fae49;
    --water-light: #e4f3fd;
    --water-mid: #a9d9f6;
    --water-deep: #5fb4ea;
  }
  * { box-sizing: border-box; margin: 0; padding: 0; }
  html, body { width: 1200px; height: 904px; overflow: hidden; }
  body {
    background: var(--bg);
    font-family: "Montserrat", sans-serif;
    position: relative;
  }
  .card {
    position: absolute;
    left: 280px;
    width: 640px;
    height: 403px;
    background: var(--card);
    border-radius: 6px;
    overflow: hidden;
    box-shadow: 0 6px 18px rgba(0,0,0,0.18);
  }
  .card--back { top: 30px; }
  .card--front { top: 471px; }
  .water {
    position: absolute;
    inset: 0;
    width: 100%;
    height: 100%;
  }
  .brand {
    position: absolute;
    display: flex;
    align-items: center;
    gap: 12px;
    color: var(--brand-blue);
    font-weight: 800;
    letter-spacing: 1px;
    text-transform: uppercase;
    white-space: nowrap;
  }
  .brand__dot {
    width: 22px; height: 22px;
    border-radius: 50%;
    background: var(--brand-blue);
  }
  .card--back .brand { left: 50%; top: 168px; transform: translateX(-50%); font-size: 30px; }
  .card--front .brand { left: 50%; top: 172px; transform: translateX(-50%); font-size: 40px; }
  .card--front .brand__dot { width: 28px; height: 28px; }
  .back__intro {
    position: absolute;
    top: 34px; left: 50px; right: 50px;
    text-align: center;
    font-weight: 700;
    font-size: 21px;
    line-height: 1.3;
    color: var(--ink);
  }
  .back__contact {
    position: absolute;
    bottom: 36px; left: 20px; right: 20px;
    text-align: center;
    font-weight: 700;
    font-size: 21px;
    line-height: 1.38;
    color: var(--ink);
  }
  .front__band {
    position: absolute;
    top: 38px; left: 30px;
    padding: 9px 26px 8px;
    border-radius: 40px;
    background: var(--band-blue);
    border-bottom: 5px solid var(--band-green);
    border-right: 5px solid var(--band-green);
    color: #fff;
    font-weight: 800;
    font-size: 22px;
    letter-spacing: 0.5px;
    white-space: nowrap;
  }
  .front__price {
    position: absolute;
    right: 36px; top: 270px;
    font-weight: 800;
    font-size: 30px;
    color: var(--ink);
  }
</style>
</head>
<body>

<section class="card card--back" aria-label="Card back">
  <svg class="water" viewBox="0 0 640 403" role="img" aria-label="Splashing water wave with bubbles">
    <defs>
      <linearGradient id="waveBack" x1="0" y1="1" x2="1" y2="0">
        <stop offset="0" stop-color="var(--water-deep)"/>
        <stop offset="0.5" stop-color="var(--water-mid)"/>
        <stop offset="1" stop-color="var(--water-light)"/>
      </linearGradient>
    </defs>
    <path d="M0 330 C120 300 220 250 330 240 C440 230 520 170 640 100 L640 403 L0 403 Z" fill="url(#waveBack)" opacity="0.55"/>
  </svg>
  <p class="back__intro">This card is to be used to access water refills at any Cedar Hollow Water Vending Machines.</p>
  <div class="brand"><span class="brand__dot"></span>Cedar Hollow</div>
  <p class="back__contact">Contact (869) 418 2930 or (869) 534 1276<br>or email clearflowbox@mailvista.example<br>for any assistance or recharging of card.</p>
</section>

<section class="card card--front" aria-label="Card front">
  <svg class="water" viewBox="0 0 640 403" role="img" aria-label="Splashing water wave with bubbles">
    <defs>
      <linearGradient id="waveFront" x1="0" y1="1" x2="1" y2="0">
        <stop offset="0" stop-color="var(--water-deep)"/>
        <stop offset="0.55" stop-color="var(--water-mid)"/>
        <stop offset="1" stop-color="var(--water-light)"/>
      </linearGradient>
    </defs>
    <path d="M0 330 C110 300 210 255 320 250 C430 245 520 170 640 90 L640 403 L0 403 Z" fill="url(#waveFront)" opacity="0.6"/>
  </svg>
  <div class="front__band">CEDAR HOLLOW WATER ATM CARD</div>
  <div class="brand"><span class="brand__dot"></span>Cedar Hollow</div>
  <p class="front__price">Price $100</p>
</section>

</body>
</html>
```